Family business needs stationery redesign with new logo

Family owned company, established in 1987 wanting a brand 'refresh'. We are an electrical, refrigeration and construction company based in the Barkly Region Northern Territory, Australia. We have a new logo we would like to use which is uploaded along with our current letterhead and email signature. We are also dropping the word 'contractors' so please do not include this on any designs. Please note also, the 'orange' color used in our logo and designs should be Northern Territory red ochre which is as follows:

RGB (Hex): #C75B12
PantoneĀ® 159 C
CMYK: 1 / 74 / 100 / 7

We are needing our stationery redesigned using our new logo. Please include letterheads, business cards, envelopes, and email signatures.

We currently use our business letterheads for quotations, invoices, letters, HR matters, and internal memos.

We also need a separate simplified letterhead for internal paperwork such as employee leave forms, meeting agendas, and meeting minutes etc.

Reason: Needing more submissions of full package designs. We are wanting all our stationery, including business cards, letterheads, email signatures, envelopes, etc to be cohesive. We also require ALL the information, as supplied on our template letterhead, to be included on the new letterhead designs. including electrical license no.etc Thank you, R&W

Reason: needing more time as work has got in the way of looking over designs. A lot of designs not meeting the brief/criteria.

Industry/Entity Type

Business

Colors
0355a3
f37122

Requirements
Must have
• The 'orange' color used in the designs should be Northern Territory red ochre which is as follows:
• RGB (Hex): #C75B12
• PantoneĀ® 159 C
• CMYK: 1 / 74 / 100 / 7
• ***MUST INCLUDE ALL INFORMATION THAT IS ON OUR CURRENT LETTERHEAD***
Should not have
• Please do not include the word 'contractors'

```html
<!DOCTYPE html>
<html lang="en">
<head>
<meta charset="utf-8">
<title>R&amp;W Business Card</title>
<link rel="stylesheet" href="https://fonts.googleapis.com/css2?family=Arimo:wght@400;700&display=swap">
<style>
  :root {
    --page: #2f2a28;
    --card: #141414;
    --card-edge: #1d1d1d;
    --brand-blue: #2a4f9c;
    --ochre: #c75b12;
    --text-light: #e6e6e6;
    --text-muted: #8a8a8a;
    --logo-grey: #9a9a9a;
    --rule: #9a9a9a;
  }
  * { box-sizing: border-box; margin: 0; padding: 0; }
  html, body { width: 1200px; height: 864px; overflow: hidden; }
  body {
    background: var(--page);
    font-family: "Arimo", Arial, sans-serif;
    position: relative;
  }
  .card {
    position: absolute;
    width: 560px;
    height: 320px;
    background: var(--card);
    border: 1px solid var(--card-edge);
    border-radius: 3px;
    box-shadow: 0 14px 30px rgba(0, 0, 0, 0.45);
  }
  .card--front { left: 40px; top: 70px; }
  .card--back { left: 600px; top: 480px; }

  .front-brand {
    position: absolute;
    left: 0; right: 0; top: 100px;
    text-align: center;
    font-weight: 700;
    font-size: 60px;
    line-height: 1;
    color: var(--logo-grey);
    letter-spacing: 1px;
  }
  .front-web {
    position: absolute;
    left: 0; right: 0; top: 198px;
    text-align: center;
    font-size: 12px;
    letter-spacing: 3px;
    color: var(--text-muted);
  }

  .back-brand {
    position: absolute;
    left: 36px; top: 128px;
    width: 210px;
    text-align: center;
    font-weight: 700;
    font-size: 56px;
    line-height: 1;
    color: var(--brand-blue);
  }
  .back-divider {
    position: absolute;
    left: 270px; top: 50px;
    width: 1px; height: 220px;
    background: linear-gradient(to bottom, transparent, var(--rule) 30%, var(--rule) 70%, transparent);
  }
  .contact {
    position: absolute;
    left: 292px; top: 62px;
    color: var(--text-light);
    font-size: 15px;
    line-height: 1.35;
  }
  .contact__name { color: var(--brand-blue); font-size: 20px; font-weight: 700; line-height: 1.15; }
  .contact__title { color: var(--ochre); font-size: 15px; margin-bottom: 10px; }
  .contact__address { margin-bottom: 8px; }
  .contact__list { list-style: none; }
  .contact__list li { display: flex; align-items: center; gap: 10px; height: 21px; white-space: nowrap; }
  .contact__icon { width: 13px; height: 13px; flex: none; }
</style>
</head>
<body>
  <section class="card card--front" aria-label="Business card front">
    <div class="front-brand">R&amp;W</div>
    <div class="front-web">www.rwbuild.com.au</div>
  </section>

  <section class="card card--back" aria-label="Business card back">
    <div class="back-brand">R&amp;W</div>
    <div class="back-divider"></div>
    <div class="contact">
      <div class="contact__name">Sam Carter</div>
      <div class="contact__title">President</div>
      <div class="contact__address">41 Ridgeway Street<br>Tennant Creek, NT 0860</div>
      <ul class="contact__list">
        <li>
          <svg class="contact__icon" viewBox="0 0 16 16" aria-hidden="true"><path fill="#2a4f9c" d="M3 1h3l1.5 4-2 1.2a9 9 0 0 0 4.3 4.3L11 8.5l4 1.5v3a2 2 0 0 1-2 2A12 12 0 0 1 1 3a2 2 0 0 1 2-2z"/></svg>
          <span>08 8962 4410</span>
        </li>
        <li>
          <svg class="contact__icon" viewBox="0 0 16 16" aria-hidden="true"><rect x="4" y="1" width="8" height="5" fill="#2a4f9c"/><rect x="1" y="6" width="14" height="7" rx="1" fill="#2a4f9c"/><rect x="4" y="11" width="8" height="4" fill="#7f9bd6"/></svg>
          <span>08 8962 4411</span>
        </li>
        <li>
          <svg class="contact__icon" viewBox="0 0 16 16" aria-hidden="true"><rect x="1" y="3" width="14" height="10" rx="1" fill="#2a4f9c"/><path d="M1.5 4l6.5 5 6.5-5" fill="none" stroke="#141414" stroke-width="1.3"/></svg>
          <span>sam@rwbuild.com.au</span>
        </li>
        <li>
          <svg class="contact__icon" viewBox="0 0 16 16" aria-hidden="true"><circle cx="8" cy="8" r="7" fill="#2a4f9c"/><path d="M1 8h14M8 1c3 3 3 11 0 14M8 1c-3 3-3 11 0 14" fill="none" stroke="#141414" stroke-width="1"/></svg>
          <span>www.rwbuild.com.au</span>
        </li>
      </ul>
    </div>
  </section>
</body>
</html>
```